Before the kettle boils, pocast with content in its majority of technology

Page dedicated to a pocast with content in its majority of technology. The page also contains the chapters of the podcast (pluggin vocalink) will also contain news. Preferably Worpress. There is already a very basic page with a simple theme, the logo and little more, I would like something more professional. Www.lamparadebolsillo.com The logo does not want to change.

Target Market(s)

Anyone

Colors

Designer to choose colors to be used in the design.

Requirements
Must have
• You can put the vocalink pluggin with the podcast chapters

```html
<!DOCTYPE html>
<html lang="en">
<head>
<meta charset="utf-8">
<title>Before the kettle boils — Technology podcast</title>
<link href="https://fonts.googleapis.com/css2?family=Oswald:wght@400;500;600&family=Open+Sans:wght@400;600;700&display=swap" rel="stylesheet">
<style>
:root{
  --orange:#f07a1a;
  --orange-dark:#d9650c;
  --ink:#222;
  --text:#555;
  --muted:#999;
  --line:#e3e3e3;
  --panel:#4a4846;
  --panel-dark:#3a3836;
  --footer:#1d1d1d;
  --white:#fff;
  --star:#f4b400;
}
*{box-sizing:border-box;margin:0;padding:0}
html,body{width:1200px;height:3673px;overflow:hidden;background:var(--white);font-family:"Open Sans",Arial,sans-serif;color:var(--text)}
a{color:inherit;text-decoration:none}

/* Hero */
.hero{position:relative;height:553px;background:linear-gradient(100deg,#3a2a22 0%,#6b4a36 35%,#8c6a52 55%,#5a4538 80%,#2e241e 100%);overflow:hidden}
.hero-photo{position:absolute;inset:0;background:radial-gradient(ellipse 320px 380px at 800px 320px,rgba(190,150,120,.55),transparent 70%)}
.topbar{position:absolute;top:0;left:0;right:0;height:110px;display:flex;align-items:center;padding:0 98px 0 120px}
.brand{display:flex;align-items:center;gap:12px;font-family:"Oswald",sans-serif;font-weight:500;font-size:20px;color:var(--orange);text-transform:uppercase;letter-spacing:.5px}
.brand-dot{width:44px;height:44px;border-radius:50%;background:var(--orange)}
.nav{margin-left:auto;display:flex;align-items:center;gap:28px;font-family:"Oswald",sans-serif;font-size:15px;color:var(--white);text-transform:uppercase}
.nav .active{color:var(--orange)}
.btn-pill{display:inline-flex;align-items:center;gap:6px;height:36px;padding:0 16px;border-radius:18px;font-family:"Oswald",sans-serif;font-size:14px;text-transform:uppercase}
.btn-login{border:2px solid var(--white);color:var(--white)}
.btn-signup{background:var(--orange);color:var(--white)}
.hero-copy{position:absolute;left:98px;top:218px;width:520px;color:var(--white)}
.hero-copy h1{font-family:"Oswald",sans-serif;font-weight:500;font-size:40px;text-transform:uppercase;letter-spacing:.5px}
.hero-copy p{margin-top:14px;font-size:17px;line-height:1.6}
.btn-start{display:inline-block;margin-top:26px;border:2px solid var(--white);border-radius:24px;padding:10px 30px;font-family:"Oswald",sans-serif;font-size:16px;text-transform:uppercase}
.dots{position:absolute;left:50%;top:487px;transform:translateX(-50%);display:flex;gap:8px}
.dots span{width:11px;height:11px;border-radius:50%;border:2px solid var(--white)}
.dots span:first-child{background:var(--white)}

/* Layout */
.page{display:flex;gap:30px;padding:70px 98px 0;height:2888px}
.main{width:627px}
.side{width:347px;padding-top:6px}
.section-title{font-family:"Oswald",sans-serif;font-weight:500;font-size:24px;color:var(--ink);text-transform:uppercase;margin-bottom:22px}

/* Episode card */
.episode{border:1px solid var(--line);box-shadow:0 1px 4px rgba(0,0,0,.08);padding:22px 0 20px;height:650px;margin-bottom:20px}
.episode.short{height:632px}
.episode h2{font-family:"Oswald",sans-serif;font-weight:500;font-size:22px;color:var(--ink);text-transform:uppercase;padding:0 18px}
.meta{display:flex;align-items:center;gap:14px;font-size:12px;color:var(--muted);padding:10px 18px 16px}
.meta .sep{color:var(--line)}
.stars{color:var(--star);letter-spacing:1px}
.ic{width:12px;height:12px;fill:var(--orange);vertical-align:-1px;margin-right:4px}
.photo{height:250px}
.player{padding:14px 18px 0}
.player-label{display:flex;align-items:center;gap:8px;font-size:10px;text-transform:uppercase;color:var(--text)}
.play{width:14px;height:14px;border-radius:50%;background:var(--orange)}
.wave{height:34px;margin-top:6px;display:block}
.excerpt{padding:22px 18px 0;font-size:12.5px;line-height:1.75;color:#666;height:112px}
.card-foot{display:flex;align-items:center;justify-content:space-between;padding:16px 18px 0}
.btn-more{border:1px solid #ccc;border-radius:18px;padding:8px 22px;font-size:12px;font-weight:700;color:var(--orange);text-transform:uppercase}
.shares{display:flex;gap:6px;font-size:11px}
.share{display:flex;border:1px solid #ccc;border-radius:3px;overflow:hidden}
.share b{font-weight:600;padding:3px 7px;background:#eef1f6;color:#3b5998}
.share i{font-style:normal;padding:3px 7px;background:var(--white)}
.view-more{display:block;font-size:13px;font-weight:700;color:var(--orange);text-transform:uppercase;margin-top:10px}

/* Sidebar */
.ad{height:253px;border:1px solid var(--line);padding:8px;margin-bottom:50px}
.ad-photo{height:100%;position:relative;background:radial-gradient(circle at 60% 40%,#b8453a,#3a2a2a 70%)}
.ad-caption{position:absolute;left:0;right:22px;top:116px;border:2px solid var(--white);background:rgba(0,0,0,.35);color:var(--white);font-family:"Oswald",sans-serif;padding:6px 10px}
.ad-caption strong{display:block;font-weight:500;font-size:24px;text-transform:uppercase}
.ad-caption span{display:block;border-top:2px solid var(--white);font-size:15px;letter-spacing:2px;text-transform:uppercase;padding-top:4px;margin-top:4px}
.widget{background:var(--panel);margin-bottom:30px;padding-bottom:20px}
.widget-tab{display:inline-block;background:var(--orange);color:var(--white);font-family:"Oswald",sans-serif;font-weight:500;font-size:19px;text-transform:uppercase;padding:8px 14px;position:relative}
.widget-tab::after{content:"";position:absolute;right:-22px;top:0;border-left:22px solid var(--orange);border-top:42px solid transparent}
.widget-rule{height:3px;background:var(--orange);margin-top:-3px}
.recent{list-style:none;padding:12px 14px 0}
.recent li{display:flex;gap:14px;height:102px}
.thumb{width:110px;height:80px;flex:none;border:3px solid var(--white)}
.recent h3{font-family:"Oswald",sans-serif;font-weight:500;font-size:17px;color:var(--white);line-height:1.3}
.recent small{display:block;margin-top:6px;font-size:11px;color:#ccc}
.widget-link{display:block;padding:6px 14px 0;font-size:12px;font-weight:700;color:var(--orange);text-transform:uppercase}
.fb-box{margin:12px 14px 0;height:150px;background:linear-gradient(120deg,#8a7a6a,#b69c82);position:relative}
.fb-name{position:absolute;left:76px;top:14px;color:var(--white);font-family:"Oswald",sans-serif;font-size:15px}
.fb-avatar{position:absolute;left:12px;top:12px;width:54px;height:54px;background:var(--orange)}
.fb-btn{position:absolute;bottom:12px;background:var(--white);color:#333;font-size:12px;font-weight:600;padding:5px 10px;border-radius:2px}
.fb-note{padding:10px 14px 0;font-size:11px;color:#ddd}
.faces{display:flex;gap:6px;padding:8px 14px 0}
.faces span{width:36px;height:36px;background:#8d8a86}
.news-input{margin:24px 14px 0;height:46px;background:var(--white);font-size:11px;color:#888;padding:15px 14px;text-transform:uppercase}
.news-btn{margin:12px 14px 0;height:44px;border:2px solid #6a6866;border-radius:22px;text-align:center;line-height:40px;font-family:"Oswald",sans-serif;font-size:16px;color:var(--orange);text-transform:uppercase}
.news-note{padding:14px 14px 0;font-size:11px;color:#ddd;line-height:1.6}
.poster{height:478px;border:1px solid var(--line);padding:6px;margin-top:40px}
.poster div{height:100%;background:linear-gradient(180deg,#1d2a4a 0%,#3d5a86 45%,#1a1e2a 100%)}
.rule{height:1px;background:var(--line);margin:-28px 0 28px}

/* Footer */
.footer{position:absolute;top:3441px;left:0;width:1200px;height:232px;background:var(--footer);border-top:4px solid var(--orange);color:#ddd}
.contacts{display:flex;justify-content:center;gap:60px;padding-top:30px;font-size:13px;line-height:1.5}
.contact{display:flex;align-items:center;gap:14px}
.contact-ic{width:40px;height:40px;border-radius:50%;background:var(--white);display:flex;align-items:center;justify-content:center}
.contact-ic svg{width:18px;height:18px;fill:#222}
.foot-nav{text-align:center;margin-top:22px;font-size:14px}
.foot-bottom{position:absolute;left:98px;right:98px;top:170px;border-top:1px solid #333;padding-top:18px;display:flex;justify-content:space-between;align-items:center;font-size:12px}
.socials{display:flex;gap:8px}
.socials span{width:28px;height:28px;border-radius:50%;border:1px solid #888}
</style>
</head>
<body>

<header class="hero">
  <div class="hero-photo" role="img" aria-label="Photo of a young woman with headphones dancing to music, blurred brick wall behind"></div>
  <div class="topbar">
    <a class="brand" href="#"><span class="brand-dot"></span>Before the kettle boils</a>
    <nav class="nav">
      <a class="active" href="#">Home</a><a href="#">Podcasts</a><a href="#">Features</a><a href="#">Pricing</a><a href="#">Program</a><a href="#">Contact</a>
      <svg width="16" height="16" viewBox="0 0 16 16"><circle cx="6.5" cy="6.5" r="5" stroke="#fff" stroke-width="2" fill="none"/><path d="M10 10l5 5" stroke="#fff" stroke-width="2"/></svg>
      <a class="btn-pill btn-login" href="#">Login</a>
      <a class="btn-pill btn-signup" href="#">Sign up</a>
    </nav>
  </div>
  <div class="hero-copy">
    <h1>Podcast de techologia</h1>
    <p>Nam libero tempore, cum soluta nobis est eligendi otio cumque nihil impedit quo minus.</p>
    <a class="btn-start" href="#">Start now!</a>
  </div>
  <div class="dots"><span></span><span></span><span></span><span></span></div>
</header>

<div class="page">
  <main class="main">
    <h2 class="section-title">Latest podcast</h2>

    <article class="episode">
      <h2>Cambio de logo</h2>
      <div class="meta"><span><svg class="ic" viewBox="0 0 12 12"><rect x="1" y="2" width="10" height="9"/></svg>19 May, 2017</span><span class="sep">|</span><span><svg class="ic" viewBox="0 0 12 12"><circle cx="6" cy="4" r="3"/><rect x="1" y="8" width="10" height="4"/></svg>de lucero</span><span class="sep">|</span><span class="stars">★★★★☆</span><span>(34 Reviews)</span></div>
      <div class="photo" style="background:linear-gradient(180deg,#f5c04a 0%,#e8962a 55%,#6a4a2a 100%)" role="img" aria-label="Person raising arms towards a sunset"></div>
      <div class="player"><div class="player-label"><span class="play"></span>Change logo</div>
        <svg class="wave" width="100%" height="34" viewBox="0 0 590 34" preserveAspectRatio="none"><rect x="0" y="8" width="560" height="18" fill="#e8642a"/><rect x="380" y="8" width="180" height="18" fill="#555"/><rect x="560" y="12" width="30" height="8" rx="4" fill="#ccc"/></svg></div>
      <p class="excerpt">Hello to all of you! Is it obvious, then? We renew the design of the logo and something on the web. Here the changes will go little by little but I will try to leave everything that I want to modify done in a week at most, everything will depend on the time that I can dedicate to him although the difficult thing is already done.</p>
      <div class="card-foot"><a class="btn-more" href="#">Read more &gt;&gt;</a><div class="shares"><span class="share"><b>Like</b><i>200</i></span><span class="share"><b>Share</b><i>200</i></span><span class="share"><b>+1</b><i>200</i></span></div></div>
    </article>

    <article class="episode">
      <h2>Do you like series? Do you know serieslab.tv?</h2>
      <div class="meta"><span><svg class="ic" viewBox="0 0 12 12"><rect x="1" y="2" width="10" height="9"/></svg>17 May, 2017</span><span class="sep">|</span><span><svg class="ic" viewBox="0 0 12 12"><circle cx="6" cy="4" r="3"/><rect x="1" y="8" width="10" height="4"/></svg>de lucero</span><span class="sep">|</span><span class="stars">★★★★☆</span><span>(34 Reviews)</span></div>
      <div class="photo" style="background:linear-gradient(100deg,#a86a3a 0%,#c88a4a 40%,#3a3a3a 70%,#8a5a32 100%)" role="img" aria-label="Yellow headphones and a phone with a play button on a wooden table"></div>
      <div class="player"><div class="player-label"><span class="play"></span>Do you like series? Do you know serieslab.tv?</div>
        <svg class="wave" width="100%" height="34" viewBox="0 0 590 34" preserveAspectRatio="none"><rect x="0" y="8" width="560" height="18" fill="#444"/><rect x="560" y="12" width="30" height="8" rx="4" fill="#ccc"/></svg></div>
      <p class="excerpt">Hello everyone! Today chapter dedicated to the lovers of the series and the films. It is the streaming video service of the website serieslab.tv portal dedicated to learning English through the method of watching movies and series in English with subtitles.</p>
      <div class="card-foot"><a class="btn-more" href="#">Read more &gt;&gt;</a><div class="shares"><span class="share"><b>Like</b><i>200</i></span><span class="share"><b>Share</b><i>200</i></span><span class="share"><b>+1</b><i>200</i></span></div></div>
    </article>

    <article class="episode">
      <h2>An advertisement and a test</h2>
      <div class="meta"><span><svg class="ic" viewBox="0 0 12 12"><rect x="1" y="2" width="10" height="9"/></svg>May 13, 2017</span><span class="sep">|</span><span><svg class="ic" viewBox="0 0 12 12"><circle cx="6" cy="4" r="3"/><rect x="1" y="8" width="10" height="4"/></svg>de lucero</span><span class="sep">|</span><span class="stars">★★★★☆</span><span>(34 Reviews)</span></div>
      <div class="photo" style="background:linear-gradient(110deg,#2a2a5a 0%,#6a4a8a 35%,#d8b890 55%,#3a3050 100%)" role="img" aria-label="Woman with headphones singing along, purple light"></div>
      <div class="player"><div class="player-label"><span class="play"></span>An advertisement and a test</div>
        <svg class="wave" width="100%" height="34" viewBox="0 0 590 34" preserveAspectRatio="none"><rect x="0" y="8" width="560" height="18" fill="#444"/><rect x="560" y="12" width="30" height="8" rx="4" fill="#ccc"/></svg></div>
      <p class="excerpt">Hello everyone! Yes, I know it has happened again, a long time since the last publication. This I have very abandoned and there is no excuse, I feel sorry but it is true, for idleness or for reasons of time I have not dedicated the attention that deserves.</p>
      <div class="card-foot"><a class="btn-more" href="#">Read more &gt;&gt;</a><div class="shares"><span class="share"><b>Like</b><i>200</i></span><span class="share"><b>Share</b><i>200</i></span><span class="share"><b>+1</b><i>200</i></span></div></div>
    </article>

    <article class="episode short">
      <h2>Security in your mail</h2>
      <div class="meta"><span><svg class="ic" viewBox="0 0 12 12"><rect x="1" y="2" width="10" height="9"/></svg>Nov 23, 2016</span><span class="sep">|</span><span><svg class="ic" viewBox="0 0 12 12"><circle cx="6" cy="4" r="3"/><rect x="1" y="8" width="10" height="4"/></svg>de lucero</span><span class="sep">|</span><span class="stars">★★★★☆</span><span>(34 Reviews)</span></div>
      <div class="photo" style="background:linear-gradient(120deg,#d8dcdc 0%,#6a7070 40%,#1a1c1c 70%,#8a9090 100%)" role="img" aria-label="Black studio headphones on a light surface"></div>
      <div class="player"><div class="player-label"><span class="play"></span>Security in your mail</div>
        <svg class="wave" width="100%" height="34" viewBox="0 0 590 34" preserveAspectRatio="none"><rect x="0" y="8" width="560" height="18" fill="#444"/><rect x="560" y="12" width="30" height="8" rx="4" fill="#ccc"/></svg></div>
      <p class="excerpt" style="height:94px">Hello everyone! Today little more to say about here said in the podcast. For those who need an extra point of security in the email is VaultMail. Free and paid plans, coding, messages that can be destroyed, etc.</p>
      <div class="card-foot"><a class="btn-more" href="#">Read more &gt;&gt;</a><div class="shares"><span class="share"><b>Like</b><i>200</i></span><span class="share"><b>Share</b><i>200</i></span><span class="share"><b>+1</b><i>200</i></span></div></div>
    </article>

    <a class="view-more" href="#">View more &gt;&gt;</a>
  </main>

  <aside class="side">
    <div class="ad"><div class="ad-photo" role="img" aria-label="Close-up of a red studio microphone">
      <div class="ad-caption"><strong>Podcast advertising</strong><span>What you need to know</span></div></div></div>

    <section class="widget">
      <div class="widget-tab">Recent posts</div><div class="widget-rule"></div>
      <ul class="recent">
        <li><div class="thumb" style="background:#2a2a2a" role="img" aria-label="Phone showing a podcast app"></div><div><h3>Un anuncio y una prueba</h3><small>13 May, 2017 · lucero</small></div></li>
        <li><div class="thumb" style="background:#7aa8b0" role="img" aria-label="Streaming series still"></div><div><h3>¿Te gustan las series? ¿Conoces serieslab.tv?</h3><small>13 May, 2017 · lucero</small></div></li>
        <li><div class="thumb" style="background:#9aa8a0" role="img" aria-label="Earbuds on a desk"></div><div><h3>Seguridad en tu Mail</h3><small>13 May, 2017 · lucero</small></div></li>
        <li><div class="thumb" style="background:#b8a890" role="img" aria-label="Tablet on a table"></div><div><h3>Kaito Tab2, calidad precio insuperable</h3><small>13 May, 2017 · lucero</small></div></li>
        <li><div class="thumb" style="background:#c89a6a" role="img" aria-label="Laptop and cloud devices"></div><div><h3>Tertulia Manzanera : Servicios en la nube</h3><small>13 May, 2017 · lucero</small></div></li>
      </ul>
      <a class="widget-link" href="#">View more &gt;&gt;</a>
    </section>
    <div class="rule"></div>

    <section class="widget" style="background:#fff;border:1px solid var(--line);padding-bottom:14px">
      <div class="widget-tab">Join our community</div><div class="widget-rule"></div>
      <div class="fb-box" role="img" aria-label="Community page cover with a road landscape">
        <div class="fb-avatar"></div><div class="fb-name">Before the kettle boils<br><small>1,695 likes</small></div>
        <span class="fb-btn" style="left:12px">Like Page</span><span class="fb-btn" style="right:12px">Sign Up</span>
      </div>
      <p class="fb-note" style="color:#777">Be the first of your friends to like this</p>
      <div class="faces"><span></span><span></span><span></span><span></span><span></span><span></span></div>
    </section>
    <div class="rule"></div>

    <section class="widget">
      <div class="widget-tab">Newsletter sign up</div><div class="widget-rule"></div>
      <div class="news-input">Enter your email address</div>
      <div class="news-btn">Sign up</div>
      <p class="news-note">By signing up, you are opting in to receive periodic communications from Before the kettle boils</p>
    </section>
    <div class="rule"></div>

    <div class="poster"><div role="img" aria-label="Film poster: a figure standing on a dark road seen in a rear-view mirror"></div></div>
  </aside>
</div>

<footer class="footer">
  <div class="contacts">
    <div class="contact"><span class="contact-ic"><svg viewBox="0 0 18 18"><path d="M9 1a6 6 0 0 0-6 6c0 5 6 10 6 10s6-5 6-10a6 6 0 0 0-6-6zm0 8a2 2 0 1 1 0-4 2 2 0 0 1 0 4z"/></svg></span><span>18 Linden Row, Suite 4<br>Harbor City, HC 20418</span></div>
    <div class="contact"><span class="contact-ic"><svg viewBox="0 0 18 18"><path d="M4 1l3 4-2 2c1 2 3 4 5 5l2-2 4 3-2 3C8 16 2 10 1 4z"/></svg></span><span>+1 555 014 2290</span></div>
    <div class="contact"><span class="contact-ic"><svg viewBox="0 0 18 18"><path d="M1 4h16v10H1zm1 1l7 5 7-5" stroke="#fff" stroke-width="1"/></svg></span><span>info@lamparadebolsillo.com</span></div>
  </div>
  <nav class="foot-nav">Home &nbsp;|&nbsp; Podcasts &nbsp;|&nbsp; Features &nbsp;|&nbsp; Pricing &nbsp;|&nbsp; Program &nbsp;|&nbsp; Contact</nav>
  <div class="foot-bottom"><span>Copyrights © 2017, Before the kettle boils . All rights reserved.</span><div class="socials"><span></span><span></span><span></span><span></span></div></div>
</footer>

</body>
</html>
```